Business Card Design for Training Business

Clear Path Coaching is a new business that delivers training and other services with a focus on topics related to mental health and wellbeing, for example, Wellmind Response Course, Resilience etc. We have a strong focus on evidence-based psychology and neuroscience. I have a logo which I will upload with the brief, so please consider colours that work well with the logo.
Target Market(s)
Adults, workplaces (particularly government and not-for-profits)
Industry/Entity Type
Business
Contact Information for Business Card
Head Strong TrainingSamantha SellwoodDirector0438 770 bec@clearpathcoaching.example.au.auwww.headstrongtraining.com.au

```html
<!DOCTYPE html>
<html lang="en">
<head>
<meta charset="utf-8">
<title>Clear Path Coaching – Business Card</title>
<link rel="stylesheet" href="https://fonts.googleapis.com/css2?family=Open+Sans:wght@400;500&family=Raleway:wght@200;300&display=swap">
<style>
  :root {
    --page: #ffffff;
    --card: #000000;
    --teal: #2bb3c0;
    --white: #ffffff;
    --soft: #d6d6d6;
  }
  html, body {
    margin: 0;
    padding: 0;
    width: 1200px;
    height: 740px;
    overflow: hidden;
    background: var(--page);
  }
  .card {
    position: absolute;
    left: 20px;
    top: 20px;
    width: 1162px;
    height: 702px;
    background: var(--card);
  }
  .card-frame {
    position: absolute;
    left: 24px;
    top: 24px;
    width: 1112px;
    height: 651px;
    border: 1px solid var(--teal);
  }
  .brand {
    position: absolute;
    right: 348px;
    top: 116px;
    text-align: right;
    font-family: "Raleway", sans-serif;
    font-weight: 200;
    color: var(--white);
  }
  .brand-main {
    display: block;
    font-size: 72px;
    line-height: 1;
    letter-spacing: 0.05em;
  }
  .brand-sub {
    display: block;
    margin-top: 18px;
    font-size: 30px;
    line-height: 1;
    letter-spacing: 0.5em;
    margin-right: -0.5em;
  }
  .brand-circle {
    position: absolute;
    left: 842px;
    top: 66px;
    width: 252px;
    height: 252px;
  }
  .person {
    position: absolute;
    left: 77px;
    top: 338px;
    font-family: "Open Sans", sans-serif;
    color: var(--white);
  }
  .person-name {
    margin: 0;
    font-size: 28px;
    font-weight: 400;
    letter-spacing: 0.1em;
    line-height: 1.1;
  }
  .person-role {
    margin: 2px 0 0;
    font-size: 19px;
    letter-spacing: 0.12em;
    line-height: 1.2;
  }
  .contacts {
    position: absolute;
    left: 76px;
    top: 448px;
    margin: 0;
    padding: 0;
    list-style: none;
    font-family: "Open Sans", sans-serif;
    font-size: 27px;
    color: var(--white);
  }
  .contact {
    display: flex;
    align-items: center;
    height: 46.5px;
  }
  .contact-icon {
    width: 31px;
    height: 31px;
    margin-right: 15px;
    flex: none;
  }
</style>
</head>
<body>
  <div class="card">
    <div class="card-frame"></div>

    <div class="brand">
      <span class="brand-main">CLEAR PATH</span>
      <span class="brand-sub">COACHING</span>
    </div>
    <svg class="brand-circle" viewBox="0 0 252 252" aria-hidden="true">
      <circle cx="126" cy="126" r="124" fill="none" stroke="var(--teal)" stroke-width="3"/>
    </svg>

    <div class="person">
      <p class="person-name">REBECCA TANFIELD</p>
      <p class="person-role">Director</p>
    </div>

    <ul class="contacts">
      <li class="contact">
        <svg class="contact-icon" viewBox="0 0 32 32" aria-hidden="true">
          <circle cx="16" cy="16" r="16" fill="var(--white)"/>
          <path d="M10.5 8.5l3 0 1.4 4-2 1.6c1 2.2 2.8 4 5 5l1.6-2 4 1.4v3c0 1-1 1.8-2 1.7C14.6 22.6 9.4 17.4 8.8 10.5c-.1-1 .7-2 1.7-2z" fill="var(--card)"/>
        </svg>
        <span>+353 1 555 0148</span>
      </li>
      <li class="contact">
        <svg class="contact-icon" viewBox="0 0 32 32" aria-hidden="true">
          <circle cx="16" cy="16" r="16" fill="var(--white)"/>
          <g fill="none" stroke="var(--card)" stroke-width="1.6">
            <circle cx="16" cy="16" r="9"/>
            <ellipse cx="16" cy="16" rx="4" ry="9"/>
            <line x1="7" y1="16" x2="25" y2="16"/>
            <line x1="16" y1="7" x2="16" y2="25"/>
            <path d="M8.8 11.5h14.4M8.8 20.5h14.4"/>
          </g>
        </svg>
        <span>www.clearpathcoaching.example.au</span>
      </li>
      <li class="contact">
        <svg class="contact-icon" viewBox="0 0 32 32" aria-hidden="true">
          <circle cx="16" cy="16" r="16" fill="var(--white)"/>
          <rect x="8" y="10.5" width="16" height="11" rx="1" fill="none" stroke="var(--card)" stroke-width="1.8"/>
          <path d="M8.5 11l7.5 6 7.5-6M8.5 21l5.5-5M23.5 21l-5.5-5" fill="none" stroke="var(--card)" stroke-width="1.6"/>
        </svg>
        <span>bec@clearpathcoaching.example.au</span>
      </li>
      <li class="contact">
        <svg class="contact-icon" viewBox="0 0 32 32" aria-hidden="true">
          <circle cx="16" cy="16" r="16" fill="var(--white)"/>
          <path d="M16 6.5a6.5 6.5 0 0 1 6.5 6.5c0 5-6.5 12.5-6.5 12.5S9.5 18 9.5 13A6.5 6.5 0 0 1 16 6.5z" fill="var(--card)"/>
          <circle cx="16" cy="13" r="2.6" fill="var(--white)"/>
        </svg>
        <span>9 Elmstead Court, Larkin Row, Dublin, D08 R417</span>
      </li>
    </ul>
  </div>
</body>
</html>
```